female esthetician looking for an impact business card

I an an expert in skin care industry with high experience in NYC.I want my business card to look professional , an impact at first look. I do want a combination between white and gold . I believe the font will be great if is gold.. The Fonts are also important. MIRABELA COSTINA (SKIN CARE BOUTIQUE)

THIS SHOULD BE THE BUSINESS NAME, and should be placed on th eback of the card.
IN front m, the name MIRABELA COSTINA - ESTHETCIAN

BY APPOINTMENTS ONLY: 518.240.7136

Target Market(s)

HIGH END CLIENTELE

Contact Information for Business Card

iT WILL BE on a luxury paper. I neeed the wow feeling

Requirements
Should not have
• pictures

```html
<!DOCTYPE html>
<html lang="en">
<head>
<meta charset="utf-8">
<title>Mirabela Costina – Skin Care Boutique Business Cards</title>
<link href="https://fonts.googleapis.com/css2?family=Lato:wght@400;700&display=swap" rel="stylesheet">
<style>
  :root {
    --canvas: #e9e5de;
    --card-white: #fcfbf7;
    --gold: #c9a233;
    --gold-band: #d8b44a;
    --gold-pale: #e9dcb4;
    --ink: #2b2b2b;
    --ink-soft: #5a5550;
  }
  * { margin: 0; padding: 0; box-sizing: border-box; }
  html, body { width: 1200px; height: 900px; overflow: hidden; }
  body {
    background: var(--canvas);
    font-family: "Lato", Arial, sans-serif;
    position: relative;
  }
  .card {
    position: absolute;
    width: 580px;
    height: 330px;
    background: var(--card-white);
    box-shadow: 0 10px 28px rgba(0,0,0,0.18);
    overflow: hidden;
  }
  .card--back { left: 110px; top: 130px; }
  .card--front { left: 510px; top: 440px; }

  .brand { position: absolute; text-align: center; }
  .brand__mark {
    width: 74px; height: 74px; border-radius: 50%;
    background: var(--gold);
    margin: 0 auto 22px;
  }
  .brand__name {
    color: var(--gold);
    font-weight: 400;
    font-size: 30px;
    letter-spacing: 3px;
    line-height: 1;
  }
  .brand__tagline {
    color: var(--gold);
    font-size: 11px;
    letter-spacing: 8px;
    margin-top: 10px;
  }
  .card--back .brand { left: 0; right: 0; top: 85px; }

  .card--front .brand { right: 28px; top: 32px; }
  .card--front .brand__mark { width: 58px; height: 58px; margin-bottom: 18px; }
  .card--front .brand__name { font-size: 24px; letter-spacing: 2px; }
  .card--front .brand__tagline { font-size: 9px; letter-spacing: 5px; margin-top: 8px; }

  .person { position: absolute; left: 40px; top: 54px; }
  .person__name { color: var(--gold); font-weight: 700; font-size: 21px; letter-spacing: 0.5px; }
  .person__title { color: var(--ink); font-size: 15px; margin-top: 2px; }

  .contact { position: absolute; left: 40px; top: 176px; list-style: none; }
  .contact__item {
    display: flex; align-items: center; gap: 8px;
    color: var(--ink); font-size: 15px; line-height: 22px;
  }
  .contact__label { color: var(--gold); font-weight: 700; font-size: 12px; letter-spacing: 0.5px; }
  .contact__icon { width: 14px; height: 14px; fill: var(--gold); flex: none; }

  .wave { position: absolute; left: 0; top: 0; width: 580px; height: 330px; }

  .address {
    position: absolute; right: 28px; top: 226px;
    color: var(--card-white); font-size: 14px; line-height: 19px;
    font-style: normal;
  }
</style>
</head>
<body>

  <section class="card card--back" aria-label="Card back">
    <div class="brand">
      <div class="brand__mark"></div>
      <p class="brand__name">MIRABELA COSTINA</p>
      <p class="brand__tagline">SKIN CARE BOUTIQUE</p>
    </div>
  </section>

  <section class="card card--front" aria-label="Card front">
    <svg class="wave" viewBox="0 0 580 330" aria-hidden="true">
      <path d="M0 258 C 120 300, 260 270, 400 200 C 470 165, 530 150, 580 146 L580 150 C 520 160, 450 185, 390 222 C 260 295, 120 312, 0 276 Z" fill="var(--gold-pale)"/>
      <path d="M0 286 C 140 322, 300 290, 420 212 C 480 176, 530 160, 580 156 L580 330 L0 330 Z" fill="var(--gold-band)"/>
    </svg>

    <div class="person">
      <p class="person__name">MIRABELA COSTINA</p>
      <p class="person__title">Esthetician</p>
    </div>

    <div class="brand">
      <div class="brand__mark"></div>
      <p class="brand__name">MIRABELA COSTINA</p>
      <p class="brand__tagline">SKIN CARE BOUTIQUE</p>
    </div>

    <ul class="contact">
      <li class="contact__item">
        <svg class="contact__icon" viewBox="0 0 16 16"><path d="M3 2h3l1.5 3.5-2 1.2a8 8 0 0 0 3.8 3.8l1.2-2L14 10v3a1 1 0 0 1-1 1A11 11 0 0 1 2 3a1 1 0 0 1 1-1z"/></svg>
        <span><span class="contact__label">BY APPOINTMENTS ONLY:</span> 518.240.7136</span>
      </li>
      <li class="contact__item">
        <svg class="contact__icon" viewBox="0 0 16 16"><path d="M1 3h14v10H1z M1 3l7 6 7-6" stroke="var(--card-white)" stroke-width="1.2"/></svg>
        hello@costinaskin.com
      </li>
      <li class="contact__item">
        <svg class="contact__icon" viewBox="0 0 16 16"><circle cx="8" cy="8" r="7"/></svg>
        www.costinaskin.com
      </li>
    </ul>

    <address class="address">
      118, Mercer Street<br>
      10012.New York, NY
    </address>
  </section>

</body>
</html>
```